holloway paving service

Needs to have phone number 0418259730 and email markholloway@brightmail.com.au.
ABN 62318470915
name mark holloway

For all your concreting solutions
Excavation
Exposed & colour concrete
House & shed slabs
Driveways
Landing & steps

Contact Information for Business Card

ph 0418259730
email markholloway@brightmail.com.au.
ABN 62318470915
name mark holloway

```html
<!DOCTYPE html>
<html lang="en">
<head>
<meta charset="utf-8">
<title>Holloway Paving Service — Business Card</title>
<link href="https://fonts.googleapis.com/css2?family=Montserrat:wght@400;500;600;700&display=swap" rel="stylesheet">
<style>
  :root {
    --orange: #f06a24;
    --grey: #626262;
    --text-grey: #5a5a5a;
    --white: #ffffff;
    --bg: #e6e6e6;
  }
  * { box-sizing: border-box; margin: 0; padding: 0; }
  html, body { width: 1200px; height: 1200px; overflow: hidden; }
  body {
    background: var(--bg);
    font-family: "Montserrat", Arial, sans-serif;
    position: relative;
  }
  .card {
    position: absolute;
    left: 100px;
    width: 1000px;
    height: 550px;
    overflow: hidden;
    box-shadow: 0 6px 18px rgba(0,0,0,0.18);
  }
  .card-back { top: 25px; background: var(--orange); }
  .card-front { top: 625px; background: var(--white); }

  /* back */
  .contact-band {
    height: 215px;
    background: var(--grey);
    display: flex;
    flex-direction: column;
    align-items: center;
    justify-content: center;
    gap: 14px;
    color: var(--white);
  }
  .phone-row { display: flex; align-items: center; gap: 24px; }
  .phone-row .rule { width: 120px; height: 2px; background: var(--white); }
  .phone-number { font-size: 46px; font-weight: 400; letter-spacing: 6px; }
  .services { padding: 36px 0 0 90px; color: var(--white); }
  .services h2 { font-size: 40px; font-weight: 700; letter-spacing: 1px; margin-bottom: 14px; }
  .services ul { list-style: none; }
  .services li {
    font-size: 34px; font-weight: 500; line-height: 1.22;
    letter-spacing: 1px; display: flex; align-items: center; gap: 22px;
  }
  .services li::before {
    content: ""; width: 16px; height: 16px; background: var(--white); flex: none;
  }

  /* front */
  .brand-block { position: absolute; left: 90px; top: 70px; display: flex; align-items: center; }
  .brand-mark { display: flex; align-items: center; gap: 12px; width: 240px; }
  .brand-mark .square { width: 26px; height: 26px; background: var(--orange); flex: none; }
  .brand-mark .mark-name { font-size: 30px; font-weight: 700; color: var(--orange); letter-spacing: 1px; }
  .divider-orange { width: 2px; height: 190px; background: var(--orange); margin: 0 40px 0 20px; }
  .company { display: flex; flex-direction: column; }
  .company-name { font-size: 46px; font-weight: 700; color: var(--orange); letter-spacing: 1px; line-height: 1; white-space: nowrap; }
  .company-sub { display: flex; align-items: center; gap: 16px; margin-top: 8px; }
  .company-sub .rule { width: 90px; height: 3px; background: var(--grey); }
  .company-sub .word { font-size: 32px; font-weight: 500; color: var(--text-grey); letter-spacing: 6px; }
  .company-phone { font-size: 32px; font-weight: 400; color: var(--orange); letter-spacing: 5px; margin-top: 6px; text-align: center; }

  .person-block { position: absolute; left: 70px; right: 40px; bottom: 80px; display: flex; align-items: center; }
  .person-name { font-size: 42px; font-weight: 700; color: var(--orange); letter-spacing: 0.5px; white-space: nowrap; flex: none; }
  .divider-grey { width: 2px; height: 130px; background: var(--grey); margin: 0 30px; flex: none; }
  .details { color: var(--text-grey); font-size: 24px; font-weight: 400; line-height: 1.8; letter-spacing: 0.5px; white-space: nowrap; }
</style>
</head>
<body>
  <section class="card card-back">
    <div class="contact-band">
      <div class="phone-row">
        <span class="rule"></span>
        <svg class="phone-icon" width="74" height="74" viewBox="0 0 74 74" aria-label="Phone">
          <circle cx="37" cy="37" r="33" fill="none" stroke="#ffffff" stroke-width="4"/>
          <path d="M27 22c2-1 4 0 5 2l3 6c1 2 0 3-1 4l-2 2c2 4 5 7 9 9l2-2c1-1 2-2 4-1l6 3c2 1 3 3 2 5l-2 3c-2 2-5 3-8 2-9-3-17-11-20-20-1-3 0-6 2-8z" fill="#ffffff"/>
        </svg>
        <span class="rule"></span>
      </div>
      <div class="phone-number">0418259730</div>
    </div>
    <div class="services">
      <h2>For all your concreting solutions</h2>
      <ul>
        <li>Excavation</li>
        <li>Exposed &amp; colour concrete</li>
        <li>House &amp; shed slabs</li>
        <li>Driveways</li>
        <li>Landing &amp; steps</li>
      </ul>
    </div>
  </section>

  <section class="card card-front">
    <div class="brand-block">
      <div class="brand-mark">
        <span class="square"></span>
        <span class="mark-name">HOLLOWAY</span>
      </div>
      <span class="divider-orange"></span>
      <div class="company">
        <div class="company-name">HOLLOWAY PAVING</div>
        <div class="company-sub">
          <span class="rule"></span>
          <span class="word">SERVICE</span>
          <span class="rule"></span>
        </div>
        <div class="company-phone">0418259730</div>
      </div>
    </div>
    <div class="person-block">
      <div class="person-name">Mark Holloway</div>
      <span class="divider-grey"></span>
      <div class="details">
        <div class="email">markholloway@brightmail.com.au</div>
        <div class="abn">ABN 62318470915</div>
      </div>
    </div>
  </section>
</body>
</html>
```